Web design for new streaming audio service

We need a homepage design for a new streaming audio service. Our company is called Dunmoral, and we’re basically Vexlo for Audiobooks, Stand-Up Comedy, Lectures, Language Learning, etc. Essentially like Plumtrek for everything audio EXCEPT music.
You don’t have to code the homepage (Design Only), but it should include 3 different designs to work with 1) Web; 2) Phones; 3) Tablets.
Below is a link to a mockup of the web version which gives a good idea of what elements we want. This is just a mockup and we want you to improve it.
Once you download the mockup, please refer to the more detailed instructions below:
The following outlines the design project for the Dunmoral homepage. We have provided a rough mockup of the homepage layout that gives you a general idea of what we’re going for. There are a few elements that we are attached to, and many others where you have complete creative freedom to do whatever you think looks good.
The ZIP file includes the following:
* Mockup to see what we have in mind (dunmoral-homepage-mockup.jpg)
* Text used (dunmoral-homepage-text.txt)
* Raw image of actor (dunmoral-actor1.jpg)
* Raw images for samples (dunmoral-sample-[name].jpg)
Although we have only provided a mockup layout for the web version, we also need you to provide a mobile phone and a tablet version of the design also. It’s very possible the tablet version may be substantially similar to the web version, but the mobile phone version will likely be much different.
All of the raw files are included in the attached ZIP file. Please use our photographs and text as provided although cropping, sizing, etc. is flexible per the instructions below.
Display Requirements:
* Web Version - Minimum resolution 1024x768 (72 dpi) but should look good on 1920x1080 (72 dpi) - Page should be designed to scale to look acceptable in all resolutions in between.
* Phone Version - Minimum Zarno 4 - 640x960 (326 dpi) but should look good on Harlow Quasar T5 - 1920x1080 (441 dpi) - Page should be designed to scale to look acceptable in all resolutions and devices in between.
* Tablet Version - Minimum Bristly Ember QX 7” - 1280x800 (216 dpi) but should also look good on a Tavo Breeze - 2048x1536 (264 dpi) - Page should be designed to scale to look acceptable in all resolutions and devices in between.
Above the Fold - We want to make sure the Dunmoral logo, Member Login Link, Large Photo, Headline, Price, Button, and the first row of sample images are all “Above the fold”. As a general guideline, this means 600 pixels high on a 1024x768 72 dpi web screen. This requirement is less important on Phone versions.
Top Logo Bar - We want to retain the blue bar with the Dunmoral logo on the page, although we are open to a different size, shape and positioning if it greatly enhances the design. Please use the standard logo color, although you are welcome to use either the horizontal or vertical orientation of the logo based on your design.
Text color, font and size - Feel free to design the text in anyway you choose as long as the text is readable on the target platforms.
Buttons - Feel free to use any size, shape and colors for the buttons as long as they are obvious and clickable relative to the page. The only exception is the Chatterly button should follow the Chatterly color scheme and logo treatment (the mockup doesn’t seem 100% correct.)
Top Photograph - We want to retain the large photograph across the top of the screen although final shape and dimensions are flexible.
Size and shape of content samples (i.e. Audiobooks, Stand-Up Comedy, etc.) - Feel free to design the content samples in anyway you choose.
Three Sales Points (i.e. Listen on your Zarno…, All you can enjoy…, etc.) - The Three Sales Points are envisioned to each have a corresponding illustration which you should provide and have rights for. The placeholder is represented by a square next to the text. The color size and shape of these elements are flexible and can be designed in any way you choose.
Opt-in form - Feel free to design the opt-in form in anyway you choose as long as the text is readable and the interactivity is obvious on the target platforms.
Text links and copyright notice - Feel free to design the bottom of the page text links and copyright notice in anyway you choose.
Additional colors, graphic design elements, etc. - Feel free to use any additional colors, graphic design elements, etc. to support your design.
people who want to listen to audio through their mobile devices.
Graphic Design

```html
<!DOCTYPE html>
<html lang="en">
<head>
<meta charset="utf-8">
<title>Dunmoral — Streaming Audio</title>
<link href="https://fonts.googleapis.com/css2?family=Open+Sans:wght@300;400;600;700&display=swap" rel="stylesheet">
<style>
:root{
  --brand-blue:#55a9d6;
  --title-blue:#4aa2d3;
  --navy:#0e3a57;
  --ink:#222;
  --muted:#555;
  --footer-bg:#ededed;
  --social:#2a2a2a;
  --chat-blue:#3558b8;
  --field:#eeeeee;
}
*{margin:0;padding:0;box-sizing:border-box}
html,body{width:727px;height:1200px;overflow:hidden;background:#fff}
body{position:relative;font-family:'Open Sans',Arial,sans-serif;color:var(--ink)}
.abs{position:absolute}

/* header */
.site-header{left:0;top:0;width:727px;height:52px;background:var(--brand-blue)}
.brand{left:86px;top:13px;display:flex;align-items:center;gap:5px;color:#fff;font-weight:700;font-size:16px;letter-spacing:-.3px}
.brand-dot{width:14px;height:14px;border-radius:50%;background:#fff}
.nav a{position:absolute;top:19px;color:#fff;font-size:11px;font-weight:400;text-decoration:none}
.member-login{left:547px;top:15px;width:70px;height:23px;background:var(--navy);color:#fff;font-size:9px;font-weight:700;display:flex;align-items:center;justify-content:center;border-radius:1px}

/* hero */
.hero{left:0;top:52px;width:727px;height:365px;background:linear-gradient(100deg,#2f4a66 0%,#5b6f87 35%,#c9b3a1 55%,#e8e6e4 75%,#f6f6f6 100%)}
.dots{left:334px;top:386px;display:flex;gap:6px}
.dots span{width:10px;height:10px;background:var(--brand-blue)}
.dots span.active{background:#fff}

/* samples */
.samples-title{left:0;top:443px;width:693px;text-align:center;font-size:14.5px;font-weight:300;color:#444}
.cover{width:134px;height:134px}
.sample-label{font-size:9px;font-weight:700;color:#222}
.listen-btn{width:82px;height:19px;border:2px solid #cfe6f3;border-radius:10px;background:var(--brand-blue);color:#fff;font-size:8px;font-weight:700;display:flex;align-items:center;justify-content:center;gap:4px}
.listen-btn svg{width:13px;height:12px}

/* sales band */
.sales-band{left:0;top:894px;width:727px;height:80px;background:var(--brand-blue)}
.point{position:absolute;top:0;width:160px;text-align:center;color:#fff;font-size:9px;font-weight:700;line-height:1.45}
.point svg{display:block;margin:14px auto 6px}

/* trial */
.trial-title{left:78px;top:992px;font-size:15px;font-weight:700;color:var(--title-blue)}
.trial-text{left:78px;top:1019px;width:300px;font-size:8.5px;line-height:1.6;color:#333}
.email-box{left:78px;top:1060px;width:280px;height:27px;background:var(--field)}
.email-box span{position:absolute;left:8px;top:8px;font-size:8px;color:#aaa}
.submit{left:293px;top:1063px;width:61px;height:19px;background:var(--brand-blue);color:#fff;font-size:8.5px;font-weight:700;display:flex;align-items:center;justify-content:center}
.card-note{left:79px;top:1093px;font-size:11px;font-weight:600;color:#222}
.divider{left:386px;top:990px;width:8px;height:140px;background:linear-gradient(90deg,rgba(0,0,0,.08),rgba(0,0,0,0))}
.access-btn{left:446px;top:1013px;width:173px;height:27px;background:linear-gradient(#555,#1d1d1d);color:#fff;font-size:8.5px;font-weight:700;display:flex;align-items:center;justify-content:center}
.or{left:446px;top:1045px;width:173px;text-align:center;font-size:13px;font-weight:600;color:#333}
.chat-btn{left:446px;top:1070px;width:173px;height:27px;background:var(--chat-blue);color:#fff;font-size:8.5px;font-weight:700;display:flex;align-items:center;gap:8px;padding-left:10px}
.chat-btn i{width:9px;height:9px;background:#fff;display:block}

/* footer */
.site-footer{left:0;top:1138px;width:727px;height:62px;background:var(--footer-bg)}
.footer-links{left:76px;top:1152px;font-size:8.5px;color:#444}
.copyright{left:76px;top:1170px;font-size:8.5px;color:#444}
.social{top:1153px;display:flex;align-items:center;gap:4px;font-size:8.5px;font-weight:600;color:var(--social)}
.social i{width:28px;height:28px;border-radius:50%;background:var(--social);display:block}
</style>
</head>
<body>

<header class="abs site-header">
  <div class="abs brand"><span class="brand-dot"></span>Dunmoral</div>
  <nav class="nav">
    <a style="left:245px">Home</a>
    <a style="left:301px">About Us</a>
    <a style="left:372px">Listen to music</a>
    <a style="left:472px">Contact us</a>
  </nav>
  <div class="abs member-login">Member Login</div>
</header>

<div class="abs hero" role="img" aria-label="Smiling young man in headphones listening on his phone"></div>
<div class="abs dots"><span class="active"></span><span></span><span></span><span></span></div>

<h2 class="abs samples-title">A sample of what you can listen on dunmoral</h2>

<!-- row 1 -->
<div class="abs cover" style="left:78px;top:479px;background:linear-gradient(#3a3a3a,#111)" role="img" aria-label="Audio book cover for a suspense novel collection"></div>
<div class="abs cover" style="left:224px;top:479px;background:linear-gradient(#f1efe6,#c9b58a)" role="img" aria-label="Stand-up comedy album cover with a boxer in a ring"></div>
<div class="abs cover" style="left:370px;top:479px;background:linear-gradient(#16202e 0 14%,#1f8fd8 14% 86%,#16202e 86%)" role="img" aria-label="Language course cover for learning French"></div>
<div class="abs cover" style="left:516px;top:479px;background:linear-gradient(#e9ecef,#d7d2cb 70%,#8fbf6a 70%)" role="img" aria-label="Biography audiobook cover with a portrait"></div>

<div class="abs sample-label" style="left:78px;top:629px">Audio books</div>
<div class="abs sample-label" style="left:224px;top:629px">Stand Up Comedy</div>
<div class="abs sample-label" style="left:370px;top:629px">Language Learning</div>
<div class="abs sample-label" style="left:514px;top:629px">Biographies &amp; Memories</div>

<div class="abs listen-btn" style="left:77px;top:649px">LISTEN NOW <svg viewBox="0 0 13 12"><path d="M1.5 9V6.5a5 5 0 0 1 10 0V9" fill="none" stroke="#fff" stroke-width="1.5"/><rect x="0.5" y="7" width="3" height="4.5" rx="1" fill="#fff"/><rect x="9.5" y="7" width="3" height="4.5" rx="1" fill="#fff"/></svg></div>
<div class="abs listen-btn" style="left:223px;top:649px">LISTEN NOW <svg viewBox="0 0 13 12"><path d="M1.5 9V6.5a5 5 0 0 1 10 0V9" fill="none" stroke="#fff" stroke-width="1.5"/><rect x="0.5" y="7" width="3" height="4.5" rx="1" fill="#fff"/><rect x="9.5" y="7" width="3" height="4.5" rx="1" fill="#fff"/></svg></div>
<div class="abs listen-btn" style="left:369px;top:649px">LISTEN NOW <svg viewBox="0 0 13 12"><path d="M1.5 9V6.5a5 5 0 0 1 10 0V9" fill="none" stroke="#fff" stroke-width="1.5"/><rect x="0.5" y="7" width="3" height="4.5" rx="1" fill="#fff"/><rect x="9.5" y="7" width="3" height="4.5" rx="1" fill="#fff"/></svg></div>
<div class="abs listen-btn" style="left:513px;top:649px">LISTEN NOW <svg viewBox="0 0 13 12"><path d="M1.5 9V6.5a5 5 0 0 1 10 0V9" fill="none" stroke="#fff" stroke-width="1.5"/><rect x="0.5" y="7" width="3" height="4.5" rx="1" fill="#fff"/><rect x="9.5" y="7" width="3" height="4.5" rx="1" fill="#fff"/></svg></div>

<!-- row 2 -->
<div class="abs cover" style="left:78px;top:685px;background:linear-gradient(#b24fb3,#7b3c93 60%,#5a2f73)" role="img" aria-label="Guided meditation cover with purple mountains"></div>
<div class="abs cover" style="left:225px;top:685px;background:linear-gradient(90deg,#3b1d12,#6a2d1a 45%,#9aa4b5 70%,#2e3340)" role="img" aria-label="Business training program cover with a speaker portrait"></div>
<div class="abs cover" style="left:371px;top:685px;background:linear-gradient(135deg,#c9a36a,#d44a5c 45%,#e9b44a 75%,#6a5a4e)" role="img" aria-label="Celebrity interview cover with a pop singer"></div>
<div class="abs cover" style="left:515px;top:685px;background:linear-gradient(#4fb6e3,#7cc9ec)" role="img" aria-label="Fitness program cover with a workout coach"></div>

<div class="abs sample-label" style="left:78px;top:824px">Guided Meditations</div>
<div class="abs sample-label" style="left:224px;top:824px">Business Training</div>
<div class="abs sample-label" style="left:370px;top:824px">Celebrity Interviews</div>
<div class="abs sample-label" style="left:514px;top:824px">Fitness Programs</div>

<div class="abs listen-btn" style="left:77px;top:846px">LISTEN NOW <svg viewBox="0 0 13 12"><path d="M1.5 9V6.5a5 5 0 0 1 10 0V9" fill="none" stroke="#fff" stroke-width="1.5"/><rect x="0.5" y="7" width="3" height="4.5" rx="1" fill="#fff"/><rect x="9.5" y="7" width="3" height="4.5" rx="1" fill="#fff"/></svg></div>
<div class="abs listen-btn" style="left:223px;top:846px">LISTEN NOW <svg viewBox="0 0 13 12"><path d="M1.5 9V6.5a5 5 0 0 1 10 0V9" fill="none" stroke="#fff" stroke-width="1.5"/><rect x="0.5" y="7" width="3" height="4.5" rx="1" fill="#fff"/><rect x="9.5" y="7" width="3" height="4.5" rx="1" fill="#fff"/></svg></div>
<div class="abs listen-btn" style="left:369px;top:846px">LISTEN NOW <svg viewBox="0 0 13 12"><path d="M1.5 9V6.5a5 5 0 0 1 10 0V9" fill="none" stroke="#fff" stroke-width="1.5"/><rect x="0.5" y="7" width="3" height="4.5" rx="1" fill="#fff"/><rect x="9.5" y="7" width="3" height="4.5" rx="1" fill="#fff"/></svg></div>
<div class="abs listen-btn" style="left:513px;top:846px">LISTEN NOW <svg viewBox="0 0 13 12"><path d="M1.5 9V6.5a5 5 0 0 1 10 0V9" fill="none" stroke="#fff" stroke-width="1.5"/><rect x="0.5" y="7" width="3" height="4.5" rx="1" fill="#fff"/><rect x="9.5" y="7" width="3" height="4.5" rx="1" fill="#fff"/></svg></div>

<!-- sales points -->
<section class="abs sales-band">
  <div class="point" style="left:65px">
    <svg width="66" height="22" viewBox="0 0 66 22">
      <rect x="2" y="1" width="13" height="20" rx="2" fill="none" stroke="#fff" stroke-width="1.8"/>
      <line x1="6" y1="18" x2="11" y2="18" stroke="#fff" stroke-width="1.5"/>
      <rect x="24" y="1" width="16" height="20" rx="2" fill="none" stroke="#fff" stroke-width="1.8"/>
      <rect x="49" y="4" width="15" height="15" fill="#fff"/>
    </svg>
    Listen on Your Zarno,Tavo or<br>Andrix device
  </div>
  <div class="point" style="left:277px">
    <svg width="30" height="22" viewBox="0 0 30 22">
      <rect x="11" y="1" width="18" height="3" fill="#fff"/><rect x="11" y="6" width="18" height="3" fill="#fff"/>
      <rect x="11" y="11" width="18" height="3" fill="#fff"/><rect x="11" y="16" width="18" height="3" fill="#fff"/>
      <circle cx="9" cy="14" r="8" fill="#fff"/>
      <text x="9" y="18" text-anchor="middle" font-size="11" font-weight="700" fill="#55a9d6" font-family="Open Sans, sans-serif">$</text>
    </svg>
    All you can enjoy for one low<br>monthly Price
  </div>
  <div class="point" style="left:478px">
    <svg width="22" height="22" viewBox="0 0 22 22">
      <circle cx="11" cy="11" r="10" fill="#fff"/>
      <path d="M7 7l8 8M15 7l-8 8" stroke="#55a9d6" stroke-width="2.4" stroke-linecap="round"/>
    </svg>
    No Obligation Cancel Anytime
  </div>
</section>

<!-- free trial -->
<h3 class="abs trial-title">Start Your Free Trail</h3>
<p class="abs trial-text">You will get instant &amp; unlimited access to al the material on dunmoral for 14 days.there is no obligation &amp; you can cancel at any time</p>
<div class="abs email-box"><span>Enter You E-mail</span></div>
<div class="abs submit">SUBMIT</div>
<div class="abs card-note">Credit Card Required For Free Trail</div>
<div class="abs divider"></div>
<div class="abs access-btn">GET AN ACCESS</div>
<div class="abs or">or</div>
<div class="abs chat-btn"><i></i>SIGN UP USING CHATTERLY</div>

<!-- footer -->
<footer class="abs site-footer"></footer>
<div class="abs footer-links">About | Help | Contact Us | Member Login | Privacy Policy | Terms &amp; Conditions</div>
<div class="abs copyright">© 2014 Dunmoral LLC -All Rights Reserved</div>
<div class="abs social" style="left:548px"><i></i>Chirply</div>
<div class="abs social" style="left:617px"><i></i>Chatterly</div>

</body>
</html>
```